Cocktail-Making Assistant App re-design

Ok boys and girls, here's the deal:
I have an android app which is almost complete, but needs a design overhaul.

The app is a standard cocktail-making assistant: gives you a list of cocktails and the ability to see which cocktail you can make out of those ingredients (drinks, fruit, etc) you have at home.

I've attached some general app flow, as well as detailed requirements/explanation presentation. Most of those things are just FYI, so that you know what it's about.

3 screens are the most important (main screen, cocktail view screen, ingredient view screen), meaning I will pick the design mostly based on ideas for those 3 things, with the fourth being a rather simple list (given on attached flow, third tier)
Some other screens are derived from that, with some minor changes on it, but you shouldn't care about that.

There are lots of other, non-explained things which I said nothing about only because they are (from design point of view) completely the same and would only make it seem more complicated.

I don't want to influence the colour scheme, but the app will be released under RedFig developer name (having a light colured red fig as a logo) so I suppose some brownish design, for example, will not really fit nicely. If you, however, have a killer which you are confident will prove me wrong, I'm looking forward to seeing it!

It should be a serious, elegant look (as opposed to cartoonish, but we are not aiming for a business look at all!), not cluttered with details, no clubbing themes, glitter and so on.

Test apk file available on request (Android 2.3+).

Edit: payment is now guaranteed
Also please note that currently, the favorite, "heart" button has a motion effect:
on click it flies out of the screen to the left (white heart) and comes back to the screen as a red heart. Take that into consideration, if it means anything to you.

Target Market(s)

Whoever you imagine would enjoy drinking cocktails

Industry/Entity Type

Business

Requirements
Must have
• Everything is said in the provided documentation - images say more than I could possibly write here.
Nice to have
• As said, most of the icons are a nice-to-have. Only those which are critically linked to the rest of the design must be provided. More details in the docs.
Should not have
• No cartoon look, No zillion colours

```html
<!DOCTYPE html>
<html lang="en">
<head>
<meta charset="utf-8">
<title>Cocktail Search</title>
<link rel="stylesheet" href="https://fonts.googleapis.com/css2?family=Michroma&display=swap">
<style>
  :root {
    --bg: #f7f7f7;
    --header-top: #ffffff;
    --header-bottom: #e6e6e6;
    --band-dark: #9e0c16;
    --band-light: #e3212b;
    --ink: #111111;
    --accent-red: #e0202a;
    --rule: #b9b9b9;
    --divider: #cfcfcf;
    --star-green: #a6d872;
    --star-orange: #f7b752;
    --star-red: #f25a5e;
    --star-purple: #b3a9ec;
    --star-beige: #d6b6ab;
    --star-off: #222222;
  }
  * { box-sizing: border-box; margin: 0; padding: 0; }
  html, body {
    width: 676px; height: 1200px; overflow: hidden;
    background: var(--bg);
    font-family: "Michroma", sans-serif;
    color: var(--ink);
  }
  .screen {
    width: 640px; height: 1136px;
    transform: scale(1.05625);
    transform-origin: 0 0;
    position: relative;
    background: var(--bg);
  }
  .app-bar {
    position: absolute; left: 0; top: 0; width: 640px; height: 92px;
    background: linear-gradient(var(--header-top), var(--header-bottom));
  }
  .app-bar .back {
    position: absolute; left: 8px; top: 36px; width: 18px; height: 26px;
  }
  .app-bar .home {
    position: absolute; left: 30px; top: 20px; width: 52px; height: 50px;
  }
  .app-bar .bar-divider {
    position: absolute; left: 124px; top: 14px; width: 1px; height: 68px;
    background: var(--divider);
  }
  .app-bar .title {
    position: absolute; left: 155px; top: 34px;
    font-size: 26px; line-height: 30px; letter-spacing: 2px;
    text-transform: uppercase; font-weight: 400;
  }
  .accent-band {
    position: absolute; left: 0; top: 92px; width: 640px; height: 9px;
    background: linear-gradient(var(--band-light), var(--band-dark));
    box-shadow: 0 2px 3px rgba(0,0,0,0.18);
  }
  .cocktail-list {
    position: absolute; left: 0; top: 172px; width: 640px;
    list-style: none;
  }
  .cocktail {
    position: relative; height: 160px; margin-left: 7px;
    border-top: 1px solid var(--rule);
  }
  .cocktail.tall { height: 164px; }
  .drink-image {
    position: absolute; left: 48px; top: 45px; width: 56px; height: 88px;
    border-radius: 4px 4px 8px 8px;
  }
  .drink-info {
    position: absolute; left: 173px; top: 0; height: 100%; width: 330px;
    display: flex; flex-direction: column; justify-content: center;
  }
  .drink-name {
    font-size: 20px; line-height: 29px; letter-spacing: 1.5px;
    text-transform: uppercase; font-weight: 400;
  }
  .rating { display: flex; gap: 6px; margin-top: 10px; margin-left: -6px; }
  .rating svg { width: 34px; height: 34px; }
  .s-green { fill: var(--star-green); }
  .s-orange { fill: var(--star-orange); }
  .s-red { fill: var(--star-red); }
  .s-purple { fill: var(--star-purple); }
  .s-beige { fill: var(--star-beige); }
  .s-off { fill: var(--star-off); }
  .stock {
    position: absolute; left: 509px; top: 34px; width: 124px; height: 92px;
    border-left: 1px solid var(--divider);
    display: flex; flex-direction: column; align-items: center;
  }
  .stock svg { width: 24px; height: 40px; margin-top: 0; }
  .stock-label {
    font-size: 14px; line-height: 21px; text-transform: uppercase;
    text-align: center; letter-spacing: 0.5px; margin-top: 8px;
  }
  .amber { background: linear-gradient(#f7d9a0, #e7a43d 40%, #d48a24); }
  .gold { background: linear-gradient(#fbfbf4, #f2e6b8 60%, #cfc39a); width: 52px; border-radius: 20px 20px 10px 10px; }
  .pink { background: linear-gradient(#f7b3b8, #e8505e 40%, #d8344a); }
  .berry { background: linear-gradient(#d4465a, #b81229 50%, #e6e6e6 70%, #cfcfcf); border-radius: 30px 30px 6px 6px; }
  .lime { background: linear-gradient(#3f7d2a, #a8cc3a 35%, #86b52b); }
  .aqua { background: linear-gradient(#c7f0a0, #34b6e0 30%, #1c8ccc); width: 42px; left: 55px; }
</style>
</head>
<body>
<svg width="0" height="0" style="position:absolute" aria-hidden="true">
  <defs>
    <symbol id="star" viewBox="0 0 24 24">
      <polygon points="12,1.5 14.6,9 22.5,9.2 16.2,14 18.5,21.8 12,17.2 5.5,21.8 7.8,14 1.5,9.2 9.4,9"/>
    </symbol>
    <symbol id="shaker" viewBox="0 0 24 40">
      <rect x="9" y="0" width="6" height="4" rx="1"/>
      <path d="M6 5 H18 L20 11 H4 Z"/>
      <rect x="2" y="12" width="20" height="3" rx="1"/>
      <path d="M2 16 H22 L19 40 H5 Z"/>
    </symbol>
  </defs>
</svg>

<div class="screen">
  <header class="app-bar">
    <svg class="back" viewBox="0 0 18 26" aria-label="Back">
      <polyline points="14,3 4,13 14,23" fill="none" stroke="var(--accent-red)" stroke-width="3"/>
    </svg>
    <svg class="home" viewBox="0 0 52 50" aria-label="Home">
      <path d="M26 2 L51 26 H44 V49 H31 V34 H21 V49 H8 V26 H1 Z" fill="var(--ink)"/>
      <rect x="37" y="5" width="7" height="12" fill="var(--ink)"/>
    </svg>
    <span class="bar-divider"></span>
    <h1 class="title">Cocktail Search</h1>
  </header>
  <div class="accent-band"></div>

  <ul class="cocktail-list">
    <li class="cocktail">
      <div class="drink-image amber" role="img" aria-label="Amber drink in a pint glass"></div>
      <div class="drink-info">
        <h2 class="drink-name">‘57 Cruiser</h2>
        <div class="rating">
          <svg class="s-green"><use href="#star"/></svg><svg class="s-orange"><use href="#star"/></svg><svg class="s-red"><use href="#star"/></svg><svg class="s-purple"><use href="#star"/></svg><svg class="s-beige"><use href="#star"/></svg>
        </div>
      </div>
      <div class="stock"><svg><use href="#shaker"/></svg><p class="stock-label">Have<br>0 of 4</p></div>
    </li>
    <li class="cocktail">
      <div class="drink-image gold" role="img" aria-label="Pale golden drink in a tasting glass"></div>
      <div class="drink-info">
        <h2 class="drink-name">‘57 Cruiser #2</h2>
        <div class="rating">
          <svg class="s-green"><use href="#star"/></svg><svg class="s-orange"><use href="#star"/></svg><svg class="s-red"><use href="#star"/></svg><svg class="s-purple"><use href="#star"/></svg><svg class="s-off"><use href="#star"/></svg>
        </div>
      </div>
      <div class="stock"><svg><use href="#shaker"/></svg><p class="stock-label">Have<br>0 of 4</p></div>
    </li>
    <li class="cocktail">
      <div class="drink-image pink" role="img" aria-label="Pink-red drink in a pint glass"></div>
      <div class="drink-info">
        <h2 class="drink-name">‘57 Cruiser with<br>a white license<br>plate</h2>
      </div>
      <div class="stock"><svg><use href="#shaker"/></svg><p class="stock-label">Have<br>0 of 4</p></div>
    </li>
    <li class="cocktail">
      <div class="drink-image berry" role="img" aria-label="Red berry drink in a wine glass with strawberry garnish"></div>
      <div class="drink-info">
        <h2 class="drink-name">1-900-MIX-MEUP</h2>
        <div class="rating">
          <svg class="s-green"><use href="#star"/></svg><svg class="s-orange"><use href="#star"/></svg><svg class="s-off"><use href="#star"/></svg><svg class="s-off"><use href="#star"/></svg><svg class="s-off"><use href="#star"/></svg>
        </div>
      </div>
      <div class="stock"><svg><use href="#shaker"/></svg><p class="stock-label">Have<br>0 of 4</p></div>
    </li>
    <li class="cocktail">
      <div class="drink-image lime" role="img" aria-label="Green drink with mint in a rocks glass"></div>
      <div class="drink-info">
        <h2 class="drink-name">110 in the shade</h2>
        <div class="rating">
          <svg class="s-green"><use href="#star"/></svg><svg class="s-off"><use href="#star"/></svg><svg class="s-off"><use href="#star"/></svg><svg class="s-off"><use href="#star"/></svg><svg class="s-off"><use href="#star"/></svg>
        </div>
      </div>
      <div class="stock"><svg><use href="#shaker"/></svg><p class="stock-label">Have<br>0 of 4</p></div>
    </li>
    <li class="cocktail tall">
      <div class="drink-image aqua" role="img" aria-label="Blue drink with lime in a highball glass"></div>
      <div class="drink-info">
        <h2 class="drink-name">151 Florida<br>Bushwacker</h2>
        <div class="rating">
          <svg class="s-off"><use href="#star"/></svg><svg class="s-off"><use href="#star"/></svg><svg class="s-off"><use href="#star"/></svg><svg class="s-off"><use href="#star"/></svg><svg class="s-off"><use href="#star"/></svg>
        </div>
      </div>
      <div class="stock"><svg><use href="#shaker"/></svg><p class="stock-label">Have<br>0 of 4</p></div>
    </li>
  </ul>
</div>
</body>
</html>
```